Website design for an Italian restaurant in Amsterdam

I need a design for a client of mine. It is for Teatro Lucerna, an Italian restaurant in Amsterdam.
We are going for a clean, modern look but we also need to realise an authentic feel.
The restaurant is located in an old movie theatre, that is where the name Teatro Lucerna comes from.
Industry/Entity Type
Italian Restaurant
Number of Pages Required
1 page
Font styles to use
Sans Serif
Colors
Designer to choose colors to be used in the design.

```html
<!DOCTYPE html>
<html lang="en">
<head>
<meta charset="utf-8">
<title>Teatro Lucerna – Italian Restaurant Amsterdam</title>
<link href="https://fonts.googleapis.com/css2?family=Cinzel:wght@400;700&family=Libre+Baskerville:wght@400;700&family=Roboto:wght@300;400;500;700&family=Yesteryear&display=swap" rel="stylesheet">
<style>
:root{
  --sand:#ae9775;
  --sand-dark:#9c8563;
  --sand-light:#c2ad8c;
  --gold:#e8b923;
  --cream:#ede3d9;
  --ink:#4a4a4a;
  --muted:#9a9a9a;
  --field:#efefef;
  --white:#ffffff;
  --wood:#f4f2ef;
}
*{margin:0;padding:0;box-sizing:border-box}
html,body{width:1200px;height:3103px;overflow:hidden}
body{position:relative;font-family:'Roboto',sans-serif;color:var(--ink);background:var(--white)}
.abs{position:absolute}
.serif-title{font-family:'Cinzel',serif;font-weight:400;letter-spacing:1px;color:#555;text-align:center}
.rule{position:absolute;height:1px;background:#cfc4b4}

/* hero */
.hero{left:0;top:0;width:1200px;height:590px;background:linear-gradient(160deg,#7a6348 0%,#5a4633 35%,#8a7457 60%,#4b3a2a 100%)}
.hero-shade{left:0;top:0;width:1200px;height:590px;background:radial-gradient(ellipse at 50% 55%,rgba(200,170,120,.35),rgba(40,28,18,.35))}
.brand-badge{left:128px;top:0;width:269px;height:100px;background:var(--white);border-radius:0 0 40px 40px / 0 0 18px 18px;border:3px solid #d8cbb6;border-top:none;display:flex;align-items:center;justify-content:center;gap:12px}
.brand-dot{width:30px;height:30px;border-radius:50%;background:#b8263a}
.brand-name{font-family:'Cinzel',serif;font-size:20px;color:#333}
.nav{left:451px;top:38px;display:flex;gap:28px;font-size:12px;color:var(--white);font-weight:500}
.hours{left:1000px;top:18px;font-size:10px;color:var(--white);display:flex;align-items:center;gap:4px}
.phone{left:912px;top:34px;font-size:19px;color:var(--white);font-weight:500}
.welcome{left:0;width:1200px;top:240px;text-align:center;font-family:'Yesteryear',cursive;font-size:78px;color:var(--white)}
.hero-title{left:0;width:1200px;top:336px;text-align:center;font-family:'Cinzel',serif;font-size:50px;color:var(--white);letter-spacing:1px}
.hero-sub{left:450px;width:300px;top:402px;text-align:center;font-size:14px;line-height:18px;color:var(--white)}
.hero-line{height:2px;background:rgba(255,255,255,.85)}

/* reserve bar */
.reserve-bar{left:0;top:590px;width:1200px;height:74px;background:var(--sand)}
.reserve-label{left:182px;top:603px;color:var(--white);line-height:20px}
.reserve-label b{display:block;font-size:20px;font-weight:700}
.reserve-label span{font-size:15px;font-weight:300}
.bar-label{font-size:14px;color:var(--white);top:618px}
.bar-field{top:611px;height:32px;background:var(--sand-light);font-size:12px;color:#efe6d8;padding:9px 16px;display:flex;justify-content:space-between;align-items:center}
.btn-gold{background:var(--gold);color:var(--white);font-weight:500;text-align:center}

/* monthly special */
.special-grid{left:200px;top:828px;width:797px;height:320px;display:grid;grid-template-columns:repeat(5,1fr);grid-template-rows:repeat(2,1fr)}
.dish-photo{background:radial-gradient(circle at 50% 55%,#c96a2a 0%,#b84d24 30%,#e9e2d6 55%,#6a5440 100%)}
.dish-photo.alt{background:radial-gradient(circle at 50% 55%,#d89540 0%,#c4752f 32%,#f2ede6 56%,#7a6a58 100%)}
.dish-photo.green{background:radial-gradient(circle at 50% 55%,#6e8a3a 0%,#b4402b 35%,#e7e2da 58%,#55453a 100%)}
.dish-card{background:#f5f5f5;text-align:center;padding-top:44px}
.dish-card h3{font-size:13px;font-weight:400;color:#555;letter-spacing:.5px}
.dish-card .mini-rule{width:44px;height:1px;background:#c9bda9;margin:10px auto 8px}
.dish-card p{font-size:8.5px;line-height:11px;color:#999;padding:0 24px}

/* sunday banner */
.sunday{left:200px;top:1231px;width:797px;height:221px;background:var(--sand);overflow:hidden}
.sunday-photo{left:0;top:0;width:797px;height:221px;background:linear-gradient(120deg,#5a4a3a,#2a2622 50%,#151515);clip-path:polygon(420px 0,797px 0,797px 221px,300px 221px)}
.sunday-kicker{left:22px;top:16px;font-size:36px;font-weight:300;color:var(--white);letter-spacing:.5px}
.sunday-title{left:22px;top:54px;font-size:38px;font-weight:700;color:var(--white)}
.sunday-hours{left:84px;top:132px;font-size:12px;color:#f4ece0;line-height:15px;display:grid;grid-template-columns:95px auto}

/* menu */
.menu{left:0;top:1533px;width:1200px;height:608px;background:linear-gradient(90deg,#ecebe8,var(--wood) 30%,#f7f6f4 70%,#efeeeb)}
.veg-photo{left:0;top:1533px;width:207px;height:540px;background:radial-gradient(circle at 30% 25%,#c4403a 0 14%,transparent 15%),radial-gradient(circle at 45% 45%,#5a8a2f 0 16%,transparent 17%),radial-gradient(circle at 25% 75%,#e9e4d8 0 16%,transparent 17%),linear-gradient(170deg,#e6c24a,#e9dfc8 55%,#d8d2c4)}
.tabs{left:389px;top:1678px;display:flex;align-items:center;font-size:13px;color:#666}
.tab{padding:5px 14px}
.tab.active{border:1px solid #999;border-radius:3px;background:#fafafa}
.categories{left:310px;top:1760px;font-size:13px;font-weight:500;color:#555}
.categories li{list-style:none;height:42px}
.cat-active{left:256px;top:1796px;width:244px;height:36px;background:#e3e1de}
.menu-panel{left:500px;top:1742px;width:441px;height:317px;background:rgba(220,216,211,.7);border-radius:6px}
.dish{left:522px;width:405px;display:flex;justify-content:space-between}
.dish h4{font-size:13px;font-weight:500;color:#444}
.dish p{font-size:10px;color:#999;line-height:13px;margin-top:2px;width:270px}
.dish .price{font-size:13px;color:#444}

/* testimonials */
.testimonials{left:0;top:2141px;width:1200px;height:290px;background:var(--cream)}
.avatar{border-radius:50%;background:linear-gradient(160deg,#d9d2c8,#b9aea0)}
.avatar.faded{opacity:.45}
.avatar.main{border:4px solid var(--white);box-shadow:0 0 0 2px #d9c9b0}
.arrow{width:26px;height:26px;border-radius:50%;background:#9b9b9b;display:flex;align-items:center;justify-content:center}
.quote-title{left:439px;top:2237px;font-family:'Libre Baskerville',serif;font-weight:700;font-size:14px;color:#333}
.quote-body{left:439px;top:2262px;width:540px;font-family:'Libre Baskerville',serif;font-size:10px;line-height:16px;color:#555}
.quote-by{left:650px;top:2308px;font-family:'Libre Baskerville',serif;font-size:10px;font-weight:700;color:#333;display:flex;align-items:center;gap:10px}
.stars{background:var(--gold);border-radius:8px;padding:2px 8px;display:flex;gap:2px}
.pager{top:2380px;height:4px}

/* contact */
.field{left:209px;width:395px;background:var(--field);font-size:10px;color:#aaa;padding:6px 10px}
.social-card{left:699px;top:2485px;width:313px;height:350px;border:1px solid #ddd;background:var(--white)}
.card-cover{left:0;top:0;width:311px;height:72px;background:linear-gradient(110deg,#1e2b3a,#3a4a60 60%,#1b2430)}
.card-food{left:0;top:150px;width:311px;height:150px;background:radial-gradient(ellipse at 45% 50%,#8a4a3a 0 20%,#e0a032 30%,#f2efe9 50%,#e7e3dc)}

/* footer */
.footer{left:0;top:2882px;width:1200px;height:186px;background:var(--sand)}
.footer-bottom{left:0;top:3068px;width:1200px;height:35px;background:var(--sand);border-top:1px solid #c3ae8d;color:#f1e8d9;font-size:9px;text-align:center;line-height:34px}
.foot-brand{left:215px;top:2973px;width:210px;text-align:center;font-family:'Cinzel',serif;font-size:20px;color:var(--white)}
.foot-address{left:195px;top:3006px;width:250px;text-align:center;font-size:10px;line-height:17px;color:var(--white)}
.foot-links{left:633px;top:3006px;font-size:10px;color:var(--white);display:flex;gap:6px}
.soc{width:14px;height:14px;border-radius:50%;background:var(--white)}
</style>
</head>
<body>

<!-- HERO -->
<div class="abs hero" role="img" aria-label="Photograph of the candle-lit restaurant dining room with set tables"></div>
<div class="abs hero-shade"></div>

<div class="abs brand-badge"><span class="brand-dot"></span><span class="brand-name">TEATRO LUCERNA</span></div>

<nav class="abs nav"><span>HOME</span><span>MENU</span><span>GROUP MENU</span><span>RESERVATION</span><span>CONTACT</span></nav>
<div class="abs hours">
  <svg width="10" height="10" viewBox="0 0 10 10"><circle cx="5" cy="5" r="4" fill="none" stroke="#fff"/><path d="M5 2.5V5h2" stroke="#fff" fill="none"/></svg>18:00 - 23:00
</div>
<div class="abs phone">(+31) 20 555 0186</div>

<div class="abs hero-line" style="left:478px;top:228px;width:244px"></div>
<div class="abs welcome">Welcome to</div>
<div class="abs hero-title">TEATRO LUCERNA</div>
<div class="abs hero-sub">The Italian restaurant located in the heart of Amsterdam</div>
<div class="abs hero-line" style="left:478px;top:470px;width:244px"></div>

<!-- RESERVE BAR -->
<div class="abs reserve-bar"></div>
<div class="abs reserve-label"><b>RESERVE</b><span>YOUR TABLE</span></div>
<svg class="abs" style="left:296px;top:590px" width="14" height="74" viewBox="0 0 14 74"><path d="M1 0V27L10 37L1 47V74" stroke="#fff" stroke-width="2" fill="none"/></svg>
<div class="abs bar-label" style="left:346px">Guests</div>
<div class="abs bar-field" style="left:416px;width:164px"><span>no. of guests</span>
  <svg width="18" height="12" viewBox="0 0 18 12"><circle cx="6" cy="3.5" r="3" fill="#fff"/><path d="M0 12c0-4 3-5 6-5s6 1 6 5z" fill="#fff"/><circle cx="13" cy="3.5" r="2.5" fill="#fff"/><path d="M13 7c3 0 5 1 5 5h-5z" fill="#fff"/></svg></div>
<div class="abs bar-label" style="left:606px">When</div>
<div class="abs bar-field" style="left:660px;width:234px"><span>select date</span>
  <svg width="12" height="12" viewBox="0 0 12 12"><rect x="1" y="2" width="10" height="9" fill="none" stroke="#fff"/><path d="M1 5h10M4 1v2M8 1v2" stroke="#fff"/></svg></div>
<div class="abs btn-gold" style="left:919px;top:610px;width:99px;height:34px;line-height:34px;font-size:12px">RESERVE</div>

<!-- MONTHLY SPECIAL -->
<div class="abs serif-title" style="left:0;width:1200px;top:730px;font-size:22px">MONTHLY SPECIAL</div>
<div class="rule" style="left:540px;top:772px;width:120px"></div>

<div class="abs special-grid">
  <div class="dish-photo" role="img" aria-label="Photo of a pasta dish with sliced meat"></div>
  <div class="dish-card"><h3>LOREM IPSUM</h3><div class="mini-rule"></div><p>Lorem ipsum dolor sit amet, consectetur adipiscing elit. Nunc at.</p></div>
  <div class="dish-photo alt" role="img" aria-label="Photo of a seafood pasta plate"></div>
  <div class="dish-card"><h3>LOREM IPSUM</h3><div class="mini-rule"></div><p>Lorem ipsum dolor sit amet, consectetur adipiscing elit. Nunc at.</p></div>
  <div class="dish-photo" role="img" aria-label="Photo of spaghetti with meatballs"></div>
  <div class="dish-card"><h3>LOREM IPSUM</h3><div class="mini-rule"></div><p>Lorem ipsum dolor sit amet, consectetur adipiscing elit. Nunc at.</p></div>
  <div class="dish-photo green" role="img" aria-label="Photo of a fresh salad with vegetables"></div>
  <div class="dish-card"><h3>LOREM IPSUM</h3><div class="mini-rule"></div><p>Lorem ipsum dolor sit amet, consectetur adipiscing elit. Nunc at.</p></div>
  <div class="dish-photo alt" role="img" aria-label="Photo of a bowl of tagliatelle"></div>
  <div class="dish-card"><h3>LOREM IPSUM</h3><div class="mini-rule"></div><p>Lorem ipsum dolor sit amet, consectetur adipiscing elit. Nunc at.</p></div>
</div>

<!-- SUNDAY BANNER -->
<section class="abs sunday">
  <div class="abs sunday-photo" role="img" aria-label="Photo of a chef plating a dish"></div>
  <svg class="abs" style="left:0;top:0" width="797" height="221" viewBox="0 0 797 221">
    <path d="M370 36H768V193H33V130" stroke="#fff" stroke-width="3" fill="none"/>
  </svg>
  <div class="abs sunday-kicker">NOW WE'RE OPEN ON</div>
  <div class="abs sunday-title">SUNDAYS</div>
  <div class="abs sunday-hours"><span>Tue - Sun</span><span>18:00 - 23:00</span><span>Mon</span><span>&nbsp;&nbsp;&nbsp;&nbsp;&nbsp;Closed</span></div>
  <div class="abs btn-gold" style="left:309px;top:133px;width:165px;height:32px;line-height:32px;font-size:13px">RESERVE A TABLE</div>
</section>

<!-- MENU -->
<section class="abs menu"></section>
<div class="abs veg-photo" role="img" aria-label="Photo of pasta, tomatoes, pepper and mushrooms on a wooden table"></div>
<div class="abs serif-title" style="left:0;width:1200px;top:1588px;font-size:22px">MENU</div>
<div class="rule" style="left:555px;top:1628px;width:90px"></div>

<div class="abs tabs">
  <span class="tab active">Foods</span>
  <span class="tab" style="margin-left:50px">Beverages</span>
  <span class="tab" style="margin-left:38px">Wines</span>
  <span class="tab" style="margin-left:40px">Deserts</span>
</div>

<div class="abs cat-active"></div>
<ul class="abs categories">
  <li>Le Insalate</li><li>Antipasti</li><li>Le Paste</li><li>Il Pesce</li><li>La Carne</li><li>Contorni</li><li>Dolce</li>
</ul>

<div class="abs menu-panel"></div>
<div class="abs dish" style="top:1758px"><div><h4>Pane Burro e Tapanada</h4><p>Bread, garlic butter and olive tapenade</p></div><span class="price">€ 4,50</span></div>
<div class="abs dish" style="top:1810px"><div><h4>Carpaccio di Manzo</h4><p>Thinly sliced tenderloin with a pesto of rocket salad and parmesan cheese</p></div><span class="price">€ 13,50</span></div>
<div class="abs dish" style="top:1878px"><div><h4>Carpaccio di Tonno</h4><p>Thinly sliced tuna with red onion, capers and rocket salad</p></div><span class="price">€ 14,50</span></div>
<div class="abs dish" style="top:1930px"><div><h4>Vitello Tonnato</h4><p>Thinly sliced veal with Piemonte tuna sauce and large capers</p></div><span class="price">€ 14,75</span></div>
<div class="abs dish" style="top:1981px"><div><h4>Antipasto Italiano</h4><p>San Daniele ham, pikante salami, Italian worst, Italian cheese, kapers, burrata en olijven (min. 2 pers.)</p></div><span class="price">€ 16,00</span></div>

<!-- TESTIMONIALS -->
<section class="abs testimonials"></section>
<div class="abs avatar faded" style="left:97px;top:2239px;width:79px;height:79px" role="img" aria-label="Guest portrait"></div>
<div class="abs avatar faded" style="left:1022px;top:2239px;width:83px;height:83px" role="img" aria-label="Guest portrait"></div>
<div class="abs arrow" style="left:204px;top:2267px"><svg width="8" height="10" viewBox="0 0 8 10"><path d="M6 1L2 5l4 4" stroke="#fff" stroke-width="2" fill="none"/></svg></div>
<div class="abs arrow" style="left:972px;top:2267px"><svg width="8" height="10" viewBox="0 0 8 10"><path d="M2 1l4 4-4 4" stroke="#fff" stroke-width="2" fill="none"/></svg></div>
<div class="abs avatar main" style="left:292px;top:2224px;width:116px;height:116px" role="img" aria-label="Portrait of reviewer Jane Doe"></div>
<div class="abs quote-title">Lorem ipsum dolor sit amet, consectetur adipiscing elit.</div>
<p class="abs quote-body">Lorem ipsum dolor sit amet, consectetur adipiscing elit. Proin interdum purus quis suscipit viverra. Etiam ullamcorper leo ac auctor aliquet. Vivamus ac dolor malesuada, viverra libero nec, accumsan ligula.</p>
<div class="abs quote-by">- Jane Doe
  <span class="stars"><svg width="56" height="9" viewBox="0 0 56 9"><g fill="#fff"><path id="s" d="M4.5 0l1.2 3h3.1l-2.5 1.9 1 3.1-2.8-2-2.8 2 1-3.1L.2 3h3.1z"/><use href="#s" x="11"/><use href="#s" x="22"/><use href="#s" x="33"/><use href="#s" x="44"/></g></svg></span>
</div>
<div class="abs pager" style="left:472px;width:83px;background:var(--gold)"></div>
<div class="abs pager" style="left:559px;width:78px;background:#a9a39b"></div>
<div class="abs pager" style="left:643px;width:81px;background:#a9a39b"></div>

<!-- CONTACT -->
<div class="abs serif-title" style="left:209px;top:2510px;font-size:22px;text-align:left">CONTACT US</div>
<div class="rule" style="left:209px;top:2548px;width:140px"></div>
<div class="abs field" style="top:2592px;height:22px">Your name</div>
<div class="abs field" style="top:2620px;height:22px">Email</div>
<div class="abs field" style="top:2648px;height:112px">Message</div>
<div class="abs btn-gold" style="left:525px;top:2768px;width:79px;height:24px;line-height:24px;font-size:10px">SEND</div>

<div class="abs social-card">
  <div class="abs card-cover" role="img" aria-label="Cover photo of the dining room at night"></div>
  <div class="abs" style="left:12px;top:22px;width:36px;height:36px;background:#fff;border:1px solid #ccc"></div>
  <div class="abs" style="left:58px;top:30px;font-size:13px;color:#fff">Teatro Lucerna</div>
  <div class="abs" style="left:10px;top:84px;width:22px;height:22px;background:#222"></div>
  <div class="abs" style="left:38px;top:84px;font-size:8px;color:#555;line-height:11px"><b>Teatro Lucerna</b><br>2 uur geleden</div>
  <div class="abs" style="left:10px;top:112px;font-size:8px;color:#444;line-height:11px">Nieuw bij Teatro Lucerna: verse huisgemaakte pasta.<br>Zin in Italiaans vanavond?<br><span style="color:#4a6ea9">teatrolucerna.info</span></div>
  <div class="abs card-food" role="img" aria-label="Photo of a plated meat dish with orange sauce"></div>
  <div class="abs" style="left:10px;top:306px;font-size:7px;color:#888">124 · 3 reacties · 1 gedeeld</div>
  <div class="abs" style="left:0;top:322px;width:311px;height:1px;background:#e5e5e5"></div>
  <div class="abs" style="left:20px;top:330px;width:270px;font-size:7px;color:#888;display:flex;justify-content:space-between"><span>Like</span><span>Comment</span><span>Share</span></div>
</div>

<!-- FOOTER -->
<footer class="abs footer"></footer>
<div class="abs" style="left:306px;top:2932px;width:28px;height:28px;border-radius:50%;border:2px solid #fff"></div>
<div class="abs foot-brand">TEATRO LUCERNA</div>
<div class="abs foot-address">Lindengracht 42, 1015KH Amsterdam<br>Tel nr.: (+31) 20 555 0186</div>
<div class="abs soc" style="left:887px;top:2974px" aria-label="Social link"></div>
<div class="abs soc" style="left:922px;top:2974px" aria-label="Social link"></div>
<div class="abs soc" style="left:955px;top:2974px" aria-label="Social link"></div>
<div class="abs foot-links"><span>Home</span><span>|</span><span>Menu</span><span>|</span><span>Group Menu</span><span>|</span><span>Reservation</span><span>|</span><span>Blog</span><span>|</span><span>Contact Us</span></div>
<div class="abs footer-bottom">Copyright teatrolucerna.info. All Right Reserved.</div>

</body>
</html>
```